Redesign 2016 Digital Marketing Website and Convert to Wordpress

Technology needed to integrate:

- redesign and convert to wordpress
- gravity forms
- malware and hacker defense / honeypot (must be very secure from hackers)
- I want gravity forms to be a flow that asks many questions with icons and progress bar.
- 1 home page design
- 1 blog design
- 1 design for internal page content
- 1 multi step gravity form
I want to focus on SMB's. We are a marketing agency thats been around since 2016.

Site is: tallpine.agency

I am looking to redesign the homepage, blog page and services page. The services page will be a template for all inner pages of the site. All content needs to be moved into the new design.

I want to get ride of the weird video.

I need you to install gravity forms pro model so we can pass utms.

I need the gravity form to be a multi step form with icons.

All "contact us" or "get a free assesments" call to actions will go to this form only.

step 1:
what is your website

step 2:
what industry are you in
- option
- Home Services
- Legal
- Ecommerce
- Lead Gen

No matter which one they select its going to produce a differnt calculator for them.

Law:
How many leads did you get last month
how much is each ase worth on average
How much revenue do you want to make

Home servicse:
How many bookings did you get last month
How much is each service worht on average
How much revenue do you wangt to make

Ecommerce:
What is your average order value
How muny purchases did you have last month
How much revenue did you drive
How much revenue do you want to drive

For lead gen:
How many leads did you get lawt month
How much revenue did they generate

Step 3:
What is your current advertising budget

step 4:
Do you have a CRM and if so what is it

Step 5:
What is your personal informagtion
name
email
phone

Let me know if this is enough to get you going

Small and medium sized law firms, ecommerce, home services and lead gen customers.

We are a digital marketing agency

• Use whats on the current site and improve upon it

• Must be very secure, developed into a wordpress website. using gravity forms. remove my photo and my staffs photo, depersonalize it so it doesnt mention me or sam crolley. Use the same color scheme. I am looking to redesign the homepage, blog page and services page. The services page will be a template for all inner pages of the site. All content needs to be moved into the new design. I want to get ride of the weird video. I need you to install gravity forms pro model so we can pass utms. I need the gravity form to be a multi step form with icons. All "contact us" or "get a free assesments" call to actions will go to this form only. step 1: what is your website step 2: what industry are you in - option - Home Services - Legal - Ecommerce - Lead Gen No matter which one they select its going to produce a differnt calculator for them. Law: How many leads did you get last month how much is each ase worth on average How much revenue do you want to make Home servicse: How many bookings did you get last month How much is each service worht on average How much revenue do you wangt to make Ecommerce: What is your average order value How muny purchases did you have last month How much revenue did you drive How much revenue do you want to drive For lead gen: How many leads did you get lawt month How much revenue did they generate How much revenue do you want to make Step 3: What is your current advertising budget step 4: Do you have a CRM and if so what is it Step 5: What is your personal informagtion name email phone Let me know if this is enough to get you going
• SHOULD NOT BE SLOPPY, I AM LOOKING FOR ATTENTION TO DETAIL.

```html
<!DOCTYPE html>
<html lang="en">
<head>
<meta charset="utf-8">
<title>Tall Pine Growth Marketing</title>
<link href="https://fonts.googleapis.com/css2?family=Montserrat:wght@300;400;500;600;700;800&display=swap" rel="stylesheet">
<style>
:root{
  --wine:#7a1417;
  --red:#9c1b1f;
  --bright:#c0201f;
  --ink:#1f1f1f;
  --text:#4a4a4a;
  --muted:#8a8a8a;
  --line:#e2e2e2;
  --soft:#f1f1f1;
  --footer:#2f2f2f;
  --white:#ffffff;
}
*{box-sizing:border-box;margin:0;padding:0}
html,body{width:1200px;height:5236px;overflow:hidden}
body{font-family:"Montserrat",sans-serif;color:var(--text);background:var(--white);position:relative}
section,header,footer{position:absolute;left:0;width:1200px;overflow:hidden}
.btn{position:absolute;display:flex;align-items:center;justify-content:center;font-weight:700;font-size:13px;letter-spacing:.3px;text-transform:uppercase;border-radius:3px;white-space:nowrap}
.btn-red{background:var(--wine);color:var(--white)}
.btn-white{background:var(--white);color:var(--wine)}
.btn-outline{border:2px solid var(--white);color:var(--white)}
.btn-outline-red{background:var(--white);color:var(--wine);box-shadow:0 2px 8px rgba(0,0,0,.18)}
.section-title{position:absolute;left:0;width:100%;text-align:center;font-size:30px;font-weight:300;color:var(--ink);letter-spacing:.5px;text-transform:uppercase}
.section-title b{font-weight:700;color:var(--wine)}
.arrow{position:absolute;width:28px;height:28px;border-radius:50%;background:var(--wine);display:flex;align-items:center;justify-content:center}

/* HERO */
.hero{top:0;height:600px;background:#1a1716}
.hero-photo{position:absolute;inset:0;background:radial-gradient(ellipse at 70% 55%,#4a3a33 0%,#221d1b 55%,#121010 100%)}
.hero-wedge{position:absolute;inset:0;background:linear-gradient(160deg,#b02024 0%,#7d1518 60%,#5a0f11 100%);clip-path:polygon(62% 0,100% 0,100% 100%,82% 100%);opacity:.92}
.nav{position:absolute;top:48px;font-size:14px;font-weight:500;color:var(--white);display:flex;gap:26px}
.nav-left{left:104px}
.nav-right{left:756px}
.brand{position:absolute;top:40px;left:502px;display:flex;align-items:center;gap:12px;color:var(--white)}
.brand-mark{width:44px;height:44px;border-radius:50%;border:2px solid var(--white)}
.brand-name{font-size:19px;font-weight:500;letter-spacing:2px;line-height:1}
.brand-sub{font-size:8px;letter-spacing:4px;margin-top:5px;font-weight:500}
.hero-cta{left:925px;top:47px;width:238px;height:40px}
.hero-title{position:absolute;left:200px;top:226px;width:600px;text-align:center;color:var(--white);font-size:46px;font-weight:400;letter-spacing:.5px}
.hero-title b{font-weight:700}
.hero-copy{position:absolute;left:270px;top:292px;width:460px;text-align:center;color:#e8e8e8;font-size:13px;line-height:23px}
.hero-btn{left:411px;top:381px;width:179px;height:40px}
.hero-dots{position:absolute;left:1141px;top:268px;display:flex;flex-direction:column;gap:12px}
.hero-dots i{width:11px;height:11px;border-radius:50%;border:2px solid var(--white);display:block}
.hero-dots i.on{background:var(--white)}

/* SERVICES CARDS */
.tradigital{top:600px;height:616px;background:var(--white)}
.tradigital .section-title{top:74px}
.card{position:absolute;top:175px;width:316px;height:370px;background:var(--white);box-shadow:0 3px 14px rgba(0,0,0,.12);text-align:center;padding:26px 28px 0}
.card.active{top:172px;box-shadow:0 8px 22px rgba(0,0,0,.2);border-bottom:5px solid var(--wine)}
.card svg{display:block;margin:0 auto}
.card h3{font-size:20px;font-weight:600;color:var(--wine);margin-top:14px}
.card p{font-size:12px;line-height:22px;color:var(--text);margin-top:10px;height:114px}
.card .btn{left:98px;bottom:32px;width:120px;height:38px;position:absolute}

/* FEATURED */
.featured{top:1216px;height:159px;background:var(--white)}
.featured-band{position:absolute;left:0;top:22px;width:1200px;height:112px;background:#e3e3e3}
.featured-tab{position:absolute;left:0;top:0;width:380px;height:159px;background:var(--wine);clip-path:polygon(0 0,100% 0,80% 100%,0 100%)}
.featured-tab span{position:absolute;left:56px;top:60px;color:var(--white);font-size:27px;font-weight:300}
.featured-tab b{font-weight:700}
.press{position:absolute;top:59px;height:51px;width:150px;background:var(--white);border-radius:3px;display:flex;align-items:center;justify-content:center;font-size:12px;font-weight:700;color:#355a8a;box-shadow:0 1px 4px rgba(0,0,0,.1)}

/* TESTIMONIALS */
.testimonials{top:1375px;height:557px;background:linear-gradient(180deg,#fafafa,#f0f0f0)}
.testimonials .section-title{top:70px;font-size:26px}
.quote{position:absolute;left:230px;top:118px;width:740px;text-align:center;font-size:17px;line-height:31px;color:#333}
.author{position:absolute;top:223px;width:100%;text-align:center;font-size:18px;font-weight:700;color:var(--wine)}
.author-site{position:absolute;top:256px;width:100%;text-align:center;font-size:13px;color:#444}
.avatars{position:absolute;top:305px;left:370px;display:flex;align-items:center;gap:14px}
.avatar{width:40px;height:40px;border-radius:50%;background:linear-gradient(135deg,#8a7a70,#4a4340)}
.avatar.big{width:72px;height:72px;border:3px solid #e0c2b4;background:linear-gradient(135deg,#c79a82,#8a5a48)}
.t-btn1{left:344px;top:410px;width:232px;height:36px}
.t-btn2{left:595px;top:410px;width:262px;height:36px}

/* MARKETING SERVICES */
.mkt{top:1932px;height:519px;background:var(--wine)}
.mkt-red{position:absolute;inset:0;background:linear-gradient(120deg,#8f191c,#6e1114)}
.mkt-photo{position:absolute;left:586px;top:0;width:614px;height:519px;background:linear-gradient(135deg,#cfcac2 0%,#8f8780 45%,#3d3632 100%);clip-path:polygon(6% 0,100% 0,100% 100%,0 100%)}
.mkt h2{position:absolute;left:108px;top:90px;color:var(--white);font-size:29px;font-weight:300;letter-spacing:.5px}
.mkt h2 b{font-weight:700}
.mkt p{position:absolute;left:104px;top:144px;width:420px;color:#f1dada;font-size:12px;line-height:25px}
.mkt .b1{left:104px;top:330px;width:238px;height:38px}
.mkt .b2{left:104px;top:383px;width:262px;height:38px}

/* WHY */
.why{top:2451px;height:681px;background:var(--white)}
.why .t1{top:80px;font-size:29px}
.why .t2{top:120px;font-size:29px;font-weight:700;color:var(--wine)}
.timeline{position:absolute;left:80px;top:320px;width:1040px;height:1px;background:#c8c8c8}
.tdot{position:absolute;top:315px;width:11px;height:11px;border-radius:50%;background:var(--wine)}
.why-col{position:absolute;top:250px;width:305px}
.why-col svg{display:block}
.why-col h3{font-size:18px;font-weight:700;color:var(--ink);line-height:26px;height:56px}
.why-col p{font-size:12.5px;line-height:25.5px;color:var(--text);margin-top:16px}

/* EBOOK */
.ebook{top:3132px;height:499px;background:linear-gradient(135deg,#f6f6f6 0%,#ebebeb 55%,#f4f4f4 100%)}
.ebook .h1{position:absolute;left:104px;top:85px;font-size:27px;font-weight:400;color:#222}
.ebook .h2{position:absolute;left:104px;top:122px;font-size:27px;font-weight:700;color:var(--wine)}
.ebook .learn{position:absolute;left:104px;top:183px;font-size:13px;font-weight:700;color:var(--wine);text-decoration:underline}
.ebook ul{position:absolute;left:104px;top:218px;list-style:none;font-size:15px;color:#333;line-height:37px}
.ebook .btn{left:104px;top:342px;width:174px;height:38px}
.ebook-circle{position:absolute;left:732px;top:170px;width:320px;height:320px;border-radius:50%;background:var(--wine)}
.ebook-cover{position:absolute;left:790px;top:110px;width:210px;height:290px;background:linear-gradient(135deg,#f4d640,#e9b820);transform:rotate(-18deg);box-shadow:6px 8px 16px rgba(0,0,0,.25)}

/* BLOG */
.blog{top:3631px;height:565px;background:var(--white)}
.blog .section-title{top:74px}
.post{position:absolute;top:156px;width:486px;height:271px}
.post.p1{left:104px;background:linear-gradient(90deg,#6a1214 0%,#6a1214 43%,#d8d4d0 43%,#9c9690 100%)}
.post.p2{left:612px;background:linear-gradient(90deg,#32b5e8 0%,#32b5e8 53%,#3a1a1a 53%,#2a1010 100%)}
.blog-dots{position:absolute;top:477px;left:573px;display:flex;gap:6px}
.blog-dots i{width:12px;height:12px;border-radius:50%;display:block;background:var(--wine)}
.blog-dots i.off{background:var(--white);border:2px solid var(--wine)}

/* PARTNERS */
.partners{top:4196px;height:289px;background:#f1f1f1}
.partners .section-title{top:84px}
.partner-row{position:absolute;top:164px;left:150px;width:900px;display:flex;justify-content:space-between;align-items:center;font-size:18px;font-weight:600;color:#6d6d6d}

/* CTA */
.cta{top:4485px;height:366px;background:linear-gradient(100deg,#7a1114 0%,#b51c1f 50%,#7a1114 100%)}
.cta .brand{left:476px;top:72px}
.cta h2{position:absolute;top:157px;width:100%;text-align:center;color:var(--white);font-size:29px;font-weight:700}
.cta p{position:absolute;top:208px;width:100%;text-align:center;color:#f2dede;font-size:13px}
.cta .b1{left:344px;top:260px;width:232px;height:38px}
.cta .b2{left:595px;top:260px;width:262px;height:38px}

/* FOOTER */
.footer{top:4851px;height:385px;background:var(--footer);color:#d4d4d4}
.fcol{position:absolute;top:67px}
.fcol h4{font-size:19px;font-weight:800;color:var(--white);margin-bottom:12px}
.fcol li{list-style:none;font-size:11px;line-height:14px;margin-bottom:14px}
.badge{position:absolute;top:108px;background:#f5f5f5;border-radius:2px}
.social{position:absolute;top:175px;left:903px;display:flex;gap:8px}
.social i{display:block;width:24px;height:24px;border-radius:50%;border:1.5px solid var(--white)}
.fline{position:absolute;left:104px;top:327px;width:992px;height:1px;background:#5a5a5a}
.copy{position:absolute;top:355px;width:100%;text-align:center;font-size:11px;color:#cfcfcf}
</style>
</head>
<body>

<header class="hero">
  <div class="hero-photo" role="img" aria-label="Dimly lit desk with a person typing on a laptop beside a coffee cup"></div>
  <div class="hero-wedge"></div>
  <nav class="nav nav-left"><span>Home</span><span>About</span><span>Industries</span><span>Services</span></nav>
  <div class="brand">
    <div class="brand-mark"></div>
    <div><div class="brand-name">TALL PINE</div><div class="brand-sub">GROWTH MARKETING</div></div>
  </div>
  <nav class="nav nav-right"><span>Blog</span><span>Contact Us</span></nav>
  <a class="btn btn-white hero-cta">Get a Free Consultation</a>
  <h1 class="hero-title">Grow Your <b>Revenue</b></h1>
  <p class="hero-copy">You've come to the right place. We've partnered with small, medium, and enterprise businesses to get the results they want through comprehensive, cohesive marketing campaigns.</p>
  <a class="btn btn-white hero-btn">Grow My Traffic</a>
  <div class="hero-dots"><i></i><i class="on"></i><i class="on"></i></div>
</header>

<section class="tradigital">
  <h2 class="section-title">Tra-Digital <b>Advertising</b></h2>
  <div class="arrow" style="left:40px;top:338px"><svg width="10" height="12" viewBox="0 0 10 12"><path d="M8 1L2 6l6 5" stroke="#fff" stroke-width="2.4" fill="none"/></svg></div>
  <div class="arrow" style="left:1130px;top:334px"><svg width="10" height="12" viewBox="0 0 10 12"><path d="M2 1l6 5-6 5" stroke="#fff" stroke-width="2.4" fill="none"/></svg></div>

  <article class="card" style="left:108px">
    <svg width="98" height="98" viewBox="0 0 98 98" fill="none" stroke="#7a1417" stroke-width="3">
      <path d="M8 80h82"/><rect x="18" y="46" width="9" height="34"/><rect x="32" y="30" width="9" height="50"/><rect x="46" y="40" width="9" height="40"/><rect x="60" y="22" width="9" height="58"/>
      <path d="M12 66l20-14 14 8 22-20 18-8"/><circle cx="80" cy="24" r="12"/><path d="M80 12v12h12"/>
    </svg>
    <h3>Analytics</h3>
    <p>There is real science behind marketing, it is not just a feeling or an art. Analytics is not only how we translate if our campaigns are successful or not, we also use it to optimize traditional media.</p>
    <a class="btn btn-red">Read More</a>
  </article>

  <article class="card active" style="left:443px">
    <svg width="98" height="98" viewBox="0 0 98 98" fill="none" stroke="#7a1417" stroke-width="3">
      <rect x="32" y="8" width="36" height="74" rx="6"/><path d="M44 14h12M46 74h8"/>
      <circle cx="22" cy="30" r="10"/><circle cx="78" cy="30" r="10"/><circle cx="22" cy="62" r="10"/><circle cx="78" cy="62" r="10"/>
      <path d="M75 66l7-4-7-4z"/><path d="M18 62h8"/>
    </svg>
    <h3>Traditional Media</h3>
    <p>John Wexford once said, "I know 50% of my advertising is working, I just don't know which half". We cracked the code to these issues of traditional advertising with proprietary</p>
    <a class="btn btn-red">Read More</a>
  </article>

  <article class="card" style="left:779px">
    <svg width="98" height="98" viewBox="0 0 98 98" fill="none" stroke="#7a1417" stroke-width="3">
      <rect x="10" y="20" width="78" height="44"/><path d="M10 14h78M30 64v24M68 64v24M20 88h60"/>
      <path d="M22 50l6-16 6 16M24 44h8"/><path d="M40 36h14M40 42h14M40 48h14"/><path d="M60 34h8a8 8 0 010 16h-8z"/>
    </svg>
    <h3>Digital Media</h3>
    <p>Combining digital marketing with your media plan can instantly grow your sales, enrollments, leads and customers. Tall Pine's paid media campaigns get roughly 3x return vs our competitors.</p>
    <a class="btn btn-red">Read More</a>
  </article>
</section>

<section class="featured">
  <div class="featured-band"></div>
  <div class="featured-tab"><span>FEATURED <b>IN :</b></span></div>
  <div class="press" style="left:376px">WebDesk News</div>
  <div class="press" style="left:545px;color:#8a2a2a;font-size:11px">Search Review Digest</div>
  <div class="press" style="left:712px;color:#222">Ping Quarterly</div>
  <div class="press" style="left:875px;color:#3a7fb0;font-size:11px">Site Builder Monthly</div>
  <div class="press" style="left:1042px;color:#222;font-size:11px">Search Signal Journal</div>
</section>

<section class="testimonials">
  <h2 class="section-title">Our Clients <b>Testimonials</b></h2>
  <p class="quote">" Tall Pine worked with us for several months and implemented many strategies we still use with success today. They are so much fun to work with and a very talented agency "</p>
  <div class="author">– Dana Whitcomb</div>
  <div class="author-site">Hollowbrook.com</div>
  <div class="avatars">
    <div class="avatar" role="img" aria-label="Client portrait"></div>
    <div class="avatar" role="img" aria-label="Client portrait"></div>
    <div class="avatar" role="img" aria-label="Client portrait"></div>
    <div class="avatar big" role="img" aria-label="Featured client portrait"></div>
    <div class="avatar" role="img" aria-label="Client portrait"></div>
    <div class="avatar" role="img" aria-label="Client portrait"></div>
    <div class="avatar" role="img" aria-label="Client portrait"></div>
    <div class="avatar" role="img" aria-label="Client portrait"></div>
  </div>
  <a class="btn btn-red t-btn1">Get a Free Consultation</a>
  <a class="btn btn-outline-red t-btn2">Give Us a Call: (480) 555-0142</a>
</section>

<section class="mkt">
  <div class="mkt-red"></div>
  <div class="mkt-photo" role="img" aria-label="Team around a wooden table with laptops, charts and reports"></div>
  <h2>OUR MARKETING <b>SERVICES</b></h2>
  <p>We believe in a holistic marketing approach where our clients benefit from our unique strategy. Combining traditional, social, content and paid media together addresses every level your potential customers may be on at any given time. Our solutions are designed and optimized to give your brand "top of mind awareness" that drives business growth up and marketing costs down.</p>
  <a class="btn btn-outline b1">Get a Free Consultation</a>
  <a class="btn btn-white b2">Give Us a Call: (480) 555-0142</a>
</section>

<section class="why">
  <h2 class="section-title t1">Why Our Clients Choose Us as Their</h2>
  <h2 class="section-title t2">Tra-Digital Marketing Agency</h2>
  <div class="timeline"></div>
  <div class="arrow" style="left:55px;top:306px"><svg width="10" height="12" viewBox="0 0 10 12"><path d="M8 1L2 6l6 5" stroke="#fff" stroke-width="2.4" fill="none"/></svg></div>
  <div class="arrow" style="left:1109px;top:306px"><svg width="10" height="12" viewBox="0 0 10 12"><path d="M2 1l6 5-6 5" stroke="#fff" stroke-width="2.4" fill="none"/></svg></div>
  <span class="tdot" style="left:103px"></span><span class="tdot" style="left:455px"></span><span class="tdot" style="left:801px"></span>

  <div class="why-col" style="left:104px;top:250px">
    <svg width="60" height="56" viewBox="0 0 60 56" fill="none" stroke="#7a1417" stroke-width="2.4"><path d="M30 10a14 14 0 00-8 25v8h16v-8a14 14 0 00-8-25z"/><path d="M24 48h12"/><circle cx="30" cy="24" r="5"/><path d="M8 20h6M46 20h6M14 6l4 4M46 6l-4 4"/></svg>
  </div>
  <div class="why-col" style="left:104px;top:357px">
    <h3>Innovative Methodologies and Technology</h3>
    <p>The type of agency that brings traditional and digital together has also created proprietary methodologies and technology to help assist in client results. These methods come from decades of experience and ingenuity.</p>
  </div>

  <div class="why-col" style="left:454px;top:250px">
    <svg width="64" height="56" viewBox="0 0 64 56" fill="none" stroke="#7a1417" stroke-width="2.4"><rect x="6" y="28" width="26" height="22"/><path d="M14 28l-4-8 22-12 8 16z"/><rect x="40" y="26" width="18" height="24"/><path d="M44 34h10M44 40h10"/></svg>
  </div>
  <div class="why-col" style="left:454px;top:357px">
    <h3>True Tra-Digital Marketing Agency</h3>
    <p>For years it has been digital vs traditional media. Well, no more! We have taken the best from both worlds to assemble state of the art and statistically proven marketing campaigns. We are the masters at blending traditional and digital together which will grow your business by 10x!</p>
  </div>

  <div class="why-col" style="left:806px;top:250px">
    <svg width="64" height="56" viewBox="0 0 64 56" fill="none" stroke="#7a1417" stroke-width="2.4"><rect x="8" y="10" width="30" height="38"/><path d="M14 20h18M14 28h18M14 36h10"/><circle cx="46" cy="14" r="8"/><rect x="38" y="30" width="20" height="18"/><path d="M42 40l4 4 8-8"/></svg>
  </div>
  <div class="why-col" style="left:806px;top:357px">
    <h3>Execution is Everything</h3>
    <p>Let's face it, ideas without execution are meaningless. How a campaign is executed, deployed and optimize makes all the difference. We learn your business and help create a presence that reflects just how amazing you truly are!</p>
  </div>
</section>

<section class="ebook">
  <div class="h1">LEARN HOW TO SKYROCKET</div>
  <div class="h2">YOUR SALES WITH SNAPLINE ADS</div>
  <div class="learn">WHAT YOU WILL LEARN:</div>
  <ul>
    <li>Learn the ins and outs of Snapline ads manager</li>
    <li>Learn best practices to skyrocket your sales</li>
    <li>Learn how to target audiences and optimize campaigns</li>
  </ul>
  <a class="btn btn-red">Download Book</a>
  <div class="ebook-circle"></div>
  <div class="ebook-cover" role="img" aria-label="Yellow ebook cover for the guide on growing sales with Snapline ads"></div>
</section>

<section class="blog">
  <h2 class="section-title">Latest <b>Blog Posts</b></h2>
  <div class="post p1" role="img" aria-label="Blog post graphic: how to improve e-commerce landing pages with paid ads data"></div>
  <div class="post p2" role="img" aria-label="Blog post graphic: the best way to track your keyword rankings"></div>
  <div class="blog-dots"><i class="off"></i><i></i><i></i></div>
</section>

<section class="partners">
  <h2 class="section-title">Strategic <b>Partners</b></h2>
  <div class="partner-row">
    <span>Searchly Ads</span><span>Beacon Ads</span><span>Searchly Metrics</span><span>AdLoop</span><span>Friendbook</span><span>Site Builder</span>
  </div>
</section>

<section class="cta">
  <div class="brand">
    <div class="brand-mark"></div>
    <div><div class="brand-name" style="font-size:24px">TALL PINE</div><div class="brand-sub">GROWTH MARKETING</div></div>
  </div>
  <h2>CAN WE HELP YOUR BUSINESS GROW?</h2>
  <p>Let's have a friendly chat to find out</p>
  <a class="btn btn-outline b1">Get a Free Consultation</a>
  <a class="btn btn-white b2">Give Us a Call: (480) 555-0142</a>
</section>

<footer class="footer">
  <div class="fcol" style="left:104px">
    <h4>SERVICES</h4>
    <ul>
      <li>Programmatic Advertising</li><li>Search Engine Marketing (SEM)</li><li>Search Engine Optimization (SEO)</li><li>Content Marketing</li><li>Email Marketing</li><li>Paid Search Advertising</li><li>Paid Social Advertising</li>
    </ul>
  </div>
  <div class="fcol" style="left:361px;width:250px">
    <h4>GUIDES</h4>
    <ul>
      <li>Ultimate Guide On Growing Your<br>Medical Practice Business</li><li>Legal Marketing Strategy Guide For<br>Law Firm Offices</li><li>Ultimate Snapline Ads Guide To<br>Skyrocket Your Leads And Sales</li><li>Ultimate Guide To Search Engine Queries</li>
    </ul>
  </div>
  <div class="fcol" style="left:665px">
    <h4>LINKS</h4>
    <ul><li>Resources</li><li>Training</li></ul>
  </div>
  <div class="badge" style="left:902px;width:124px;height:42px"></div>
  <div class="badge" style="left:1038px;top:104px;width:48px;height:48px;border-radius:50%"></div>
  <div class="social"><i></i><i></i><i></i><i></i><i></i></div>
  <div class="fline"></div>
  <div class="copy">© 2024 Tall Pine. All rights reserved</div>
</footer>

</body>
</html>
```